Valderons Business Card

Business card for philanthropic organization

Industry/Entity Type

Business

Contact Information for Business Card

Need a very ELEGANT, sober, embossed, formal business card... it should transmit CREDIBILITY. Not looking for a "fun card". would like white, grays or black designs.

Font styles to use
Script

Requirements
Must have
• Embossed look

```html
<!DOCTYPE html>
<html lang="en">
<head>
<meta charset="utf-8">
<title>Valderons Business Card</title>
<link href="https://fonts.googleapis.com/css2?family=Andika&family=Tangerine:wght@400;700&display=swap" rel="stylesheet">
<style>
  :root {
    --backdrop: #e4e4e2;
    --card-top: #ffffff;
    --card-bottom: #eeeeee;
    --ink: #3a3a3a;
    --ink-soft: #8a8a8a;
    --rule: #4a4a4a;
    --emboss-light: rgba(255,255,255,0.95);
    --emboss-dark: rgba(0,0,0,0.18);
  }
  * { margin: 0; padding: 0; box-sizing: border-box; }
  html, body {
    width: 1200px; height: 1023px; overflow: hidden;
    background: var(--backdrop);
  }
  .stage {
    width: 1200px; height: 1023px;
    display: flex; align-items: center; justify-content: center;
  }
  .card {
    position: relative;
    width: 1000px; height: 572px;
    border-radius: 22px;
    background: linear-gradient(160deg, var(--card-top) 0%, #f7f7f7 55%, var(--card-bottom) 100%);
    box-shadow: 0 2px 0 #d6d6d6, 0 4px 0 #e8e8e8, 0 6px 0 #d0d0d0, 0 20px 40px rgba(0,0,0,0.18);
    font-family: 'Andika', sans-serif;
    color: var(--ink);
  }
  .embossed {
    text-shadow: -1px -1px 0 var(--emboss-light), 1px 1px 1px var(--emboss-dark);
  }
  .member-block {
    position: absolute; left: 64px; top: 60px;
    font-size: 30px; line-height: 1.32;
  }
  .member-block .member-name { color: var(--ink-soft); }
  .brand {
    position: absolute; right: 70px; top: 70px;
    display: flex; align-items: center; gap: 14px;
    font-size: 30px; color: var(--ink);
  }
  .brand-dot {
    width: 22px; height: 22px; border-radius: 50%;
    background: #9a9a9a;
    box-shadow: inset -1px -1px 2px rgba(0,0,0,0.3), inset 1px 1px 2px rgba(255,255,255,0.6);
  }
  .holder {
    position: absolute; left: 64px; top: 250px;
  }
  .holder-name {
    font-family: 'Tangerine', cursive;
    font-weight: 400; font-size: 92px; line-height: 1;
    color: #4a4a4a;
  }
  .holder-role {
    font-family: 'Tangerine', cursive;
    font-size: 34px; color: var(--ink-soft);
    margin-left: 42px; margin-top: -6px;
  }
  .divider {
    position: absolute; left: 64px; right: 64px; top: 412px;
    height: 2px; background: var(--rule);
    box-shadow: 0 1px 0 var(--emboss-light);
  }
  .contact {
    position: absolute; left: 64px; top: 436px;
    font-size: 24px; line-height: 1.5;
  }
  .contact li { list-style: none; display: flex; align-items: center; gap: 12px; }
  .contact svg { width: 18px; height: 18px; flex: none; }
  .address {
    position: absolute; right: 64px; top: 436px;
    font-size: 24px; line-height: 1.5; text-align: right;
  }
</style>
</head>
<body>
<main class="stage">
  <article class="card">
    <div class="member-block embossed">
      <p class="member-name">Marcel Ordaz</p>
      <p>Alba Serene Valderons</p>
      <p>Potentate 2017</p>
    </div>

    <div class="brand embossed">
      <span class="brand-dot"></span>
      <span>Valderons</span>
    </div>

    <div class="holder embossed">
      <p class="holder-name">Daniel Serra</p>
      <p class="holder-role">Director</p>
    </div>

    <div class="divider"></div>

    <ul class="contact embossed">
      <li>
        <svg viewBox="0 0 24 24" aria-hidden="true"><path d="M6.6 10.8a15 15 0 006.6 6.6l2.2-2.2c.3-.3.7-.4 1-.2 1.1.4 2.3.6 3.6.6.6 0 1 .4 1 1V20c0 .6-.4 1-1 1A17 17 0 013 4c0-.6.4-1 1-1h3.5c.6 0 1 .4 1 1 0 1.3.2 2.5.6 3.6.1.3 0 .7-.2 1z" fill="#444"/></svg>
        +(500)-4210-7733
      </li>
      <li>
        <svg viewBox="0 0 24 24" aria-hidden="true"><rect x="3" y="5" width="18" height="14" rx="1.5" fill="none" stroke="#444" stroke-width="2"/><path d="M3 6l9 7 9-7" fill="none" stroke="#444" stroke-width="2"/></svg>
        marcelordaz@mailbox.com
      </li>
    </ul>

    <div class="address embossed">
      <p>P.O. Box 0120-44871</p>
      <p>Port Lune, Republic of Verano</p>
    </div>
  </article>
</main>
</body>
</html>
```